RWT Fittings Ltd Business Cards

We need a business card with our business logo. We provide window and door installations on high-rises in west coast British Colombia, Canada.

I would like my business information and details on one side of the card, and the other side the company name with logo

Target Market(s)

General Contractors

Industry/Entity Type

Construction

Contact Information for Business Card

one side i want my company name and logo in the dark theme logo that i provided

Requirements
Must have
• Marco Peltieri, 16045518293, RWTFittings@mailbox-demo.com, 1407-5194 Linden Row Burnaby BC, V5H 2K9, Owner & Manager

```html
<!DOCTYPE html>
<html lang="en">
<head>
<meta charset="utf-8">
<title>RWT Fittings Ltd Business Cards</title>
<link rel="stylesheet" href="https://fonts.googleapis.com/css2?family=Roboto:wght@400;500;700&display=swap">
<style>
  :root {
    --backdrop: #232325;
    --card: #1f2026;
    --card-edge: #17181c;
    --accent: #29abe2;
    --name-grey: #a7a9ac;
    --text-light: #e6e7e8;
    --emboss: #3b3e46;
  }
  * { margin: 0; padding: 0; box-sizing: border-box; }
  html, body {
    width: 1200px;
    height: 780px;
    overflow: hidden;
    background: var(--backdrop);
  }
  .canvas {
    position: relative;
    width: 1200px;
    height: 780px;
    display: flex;
    align-items: center;
    justify-content: center;
    gap: 60px;
    font-family: "Roboto", Arial, sans-serif;
  }
  .card {
    position: relative;
    width: 525px;
    height: 300px;
    background: var(--card);
    border: 1px solid var(--card-edge);
    box-shadow: 0 18px 40px rgba(0, 0, 0, 0.45);
    overflow: hidden;
  }

  /* Contact side */
  .contact-block {
    position: absolute;
    left: 40px;
    top: 40px;
    padding-left: 14px;
  }
  .contact-block::before {
    content: "";
    position: absolute;
    left: 0;
    top: 4px;
    width: 5px;
    height: 34px;
    background: var(--accent);
  }
  .person-name {
    font-size: 28px;
    font-weight: 700;
    line-height: 1.15;
    color: var(--name-grey);
  }
  .person-name .first { color: var(--accent); }
  .person-role {
    font-size: 13px;
    color: var(--text-light);
    margin-top: 4px;
  }
  .address {
    font-size: 13px;
    line-height: 1.45;
    color: var(--text-light);
    margin-top: 12px;
    font-style: normal;
  }
  .contact-line {
    display: flex;
    align-items: center;
    gap: 8px;
    font-size: 13px;
    color: var(--text-light);
    margin-top: 6px;
  }
  .contact-line:first-of-type { margin-top: 12px; }
  .contact-line svg { width: 12px; height: 12px; flex: none; }

  .brand-front {
    position: absolute;
    right: 34px;
    bottom: 34px;
    display: flex;
    align-items: center;
    gap: 12px;
  }
  .brand-mark {
    width: 34px;
    height: 34px;
    background: var(--accent);
  }
  .brand-name {
    font-size: 30px;
    font-weight: 700;
    letter-spacing: 1px;
    color: var(--accent);
  }

  /* Logo side */
  .card-logo {
    display: flex;
    align-items: center;
    justify-content: center;
  }
  .brand-back .brand-name {
    font-size: 40px;
    color: var(--emboss);
  }
</style>
</head>
<body>
<main class="canvas">
  <section class="card card-contact" aria-label="Business card, contact side">
    <div class="contact-block">
      <h1 class="person-name"><span class="first">Marco</span> Peltieri</h1>
      <p class="person-role">Owner &amp; Manager</p>
      <address class="address">1407-5194 Linden Row<br>Burnaby BC, V5H 2K9</address>
      <p class="contact-line">
        <svg viewBox="0 0 24 24" aria-hidden="true"><path fill="#29abe2" d="M6.6 10.8a15.1 15.1 0 0 0 6.6 6.6l2.2-2.2a1 1 0 0 1 1-.25 11.4 11.4 0 0 0 3.6.57 1 1 0 0 1 1 1V20a1 1 0 0 1-1 1A17 17 0 0 1 3 4a1 1 0 0 1 1-1h3.5a1 1 0 0 1 1 1c0 1.25.2 2.46.57 3.6a1 1 0 0 1-.25 1z"/></svg>
        1604 551 8293
      </p>
      <p class="contact-line">
        <svg viewBox="0 0 24 24" aria-hidden="true"><path fill="#29abe2" d="M3 5h18a1 1 0 0 1 1 1v12a1 1 0 0 1-1 1H3a1 1 0 0 1-1-1V6a1 1 0 0 1 1-1zm1 2.4V17h16V7.4l-8 5.2z"/></svg>
        RWTFittings@mailbox-demo.com
      </p>
    </div>
    <div class="brand-front">
      <span class="brand-mark" aria-hidden="true"></span>
      <span class="brand-name">RWT Fittings Ltd</span>
    </div>
  </section>

  <section class="card card-logo" aria-label="Business card, logo side">
    <div class="brand-back">
      <span class="brand-name">RWT Fittings Ltd</span>
    </div>
  </section>
</main>
</body>
</html>
```